Business Card Design Project - Brindle Works

We need a new business card that fits with our new logo. We are a social media agency and consultancy operating in China. We want a fresh and strong business card. Our cards need to be two-sided as we have both English and Chinese language names and addresses on the card, but as with our current business card this does not need to be a mirror-image. Our thoughts go out to a white card on the front where the logo/name is and then using the logo colours for different coloured back-grounds. i.e that the back of the biz card works with the four different colours in the logo.

Attached is the new logo, and also a copy of our old business cards.

Target Market(s)

CEO's, CMO's. media and advertising professionals

Industry/Entity Type

Business

Requirements
Must have
• inclusion of both Chinese and English language
Nice to have
• four different colored versions of the back of the biz card. Our logo has four colors and each of these colors we would like to have a version of.

```html
<!DOCTYPE html>
<html lang="en">
<head>
<meta charset="utf-8">
<title>Brindle Works — Business Cards</title>
<link href="https://fonts.googleapis.com/css2?family=Questrial&family=Open+Sans:wght@400;700&family=Noto+Sans+SC:wght@500;700&display=swap" rel="stylesheet">
<style>
  :root{
    --green:#8cc63f;
    --purple:#662d91;
    --pink:#ec008c;
    --orange:#f15a24;
    --ink:#1a1a1a;
    --grey:#555555;
    --paper:#ffffff;
    --page:#ffffff;
  }
  *{margin:0;padding:0;box-sizing:border-box}
  html,body{width:1200px;height:977px;overflow:hidden;background:var(--page)}
  .sheet{position:relative;width:1200px;height:977px}
  .card{
    position:absolute;width:222px;height:361px;
    box-shadow:2px 3px 6px rgba(0,0,0,.22);
    overflow:hidden;
  }
  .set-green{--accent:var(--green)}
  .set-purple{--accent:var(--purple)}
  .set-pink{--accent:var(--pink)}
  .set-orange{--accent:var(--orange)}
  .front{background:var(--paper);color:var(--ink)}
  .back{background:var(--accent);color:var(--paper)}

  .wordmark{
    position:absolute;left:12px;top:34px;
    display:flex;align-items:center;gap:7px;
    font-family:"Questrial",sans-serif;font-size:27px;line-height:1;
    letter-spacing:-.5px;white-space:nowrap;
  }
  .front .wordmark{color:var(--ink)}
  .back .wordmark{color:var(--paper)}
  .wordmark .dot{width:9px;height:9px;background:var(--accent);flex:none}
  .back .wordmark .dot{background:var(--paper)}

  .person{position:absolute;left:13px;top:158px}
  .person-name{font-family:"Questrial",sans-serif;font-size:27px;line-height:1;letter-spacing:-.3px}
  .person-role{font-family:"Questrial",sans-serif;font-size:14px;line-height:1.1;color:var(--grey);margin-top:1px}

  .contacts{
    position:absolute;left:13px;top:212px;
    font-family:"Open Sans",sans-serif;font-size:10px;line-height:12px;
    display:grid;grid-template-columns:44px auto;
  }
  .contacts dt{color:var(--accent);font-weight:700}
  .contacts dd{color:var(--ink)}

  .palette{position:absolute;left:13px;top:335px;display:flex;gap:2px}
  .palette span{width:48px;height:15px}

  .cn-name{
    position:absolute;left:13px;top:156px;
    font-family:"Noto Sans SC",sans-serif;font-weight:700;font-size:25px;line-height:1;
    display:flex;align-items:baseline;gap:12px;
  }
  .cn-name small{font-size:13px;font-weight:500}
  .address{position:absolute;left:13px;top:205px;font-family:"Noto Sans SC","Open Sans",sans-serif;font-size:7.5px;line-height:10.5px;font-weight:500}
  .address p+p{margin-top:0}
  .address .en{font-family:"Open Sans",sans-serif;font-weight:700;margin-top:3px}
  .web{position:absolute;left:12px;top:331px;font-family:"Open Sans",sans-serif;font-size:18.5px;line-height:1;letter-spacing:-.2px}
</style>
</head>
<body>
<main class="sheet">

  <!-- green set -->
  <article class="card front set-green" style="left:40px;top:38px">
    <div class="wordmark"><span>Brindle Works</span><span class="dot"></span></div>
    <div class="person"><p class="person-name">Owen Hartley</p><p class="person-role">managing director</p></div>
    <dl class="contacts"><dt>email:</dt><dd>owen@hartleymail.com</dd><dt>skype:</dt><dd>owenbeijing</dd><dt>mobile:</dt><dd>+86 13800452718</dd></dl>
    <div class="palette"><span style="background:var(--green)"></span><span style="background:var(--purple)"></span><span style="background:var(--pink)"></span><span style="background:var(--orange)"></span></div>
  </article>
  <article class="card back set-green" style="left:299px;top:38px">
    <div class="wordmark"><span>Brindle Works</span><span class="dot"></span></div>
    <div class="cn-name"><span>何欧文</span><small>董事总经理</small></div>
    <div class="address"><p>灯笼庭商务中心C310室 东河路</p><p>北京市朝阳区 (100020)</p><p class="en">Suite C310, Lantern Court Business Centre</p><p class="en" style="margin-top:0">Donghe Road Chaoyang District, Beijing 100020</p></div>
    <p class="web">www.brindlechina.com</p>
  </article>

  <!-- purple set -->
  <article class="card front set-purple" style="left:678px;top:38px">
    <div class="wordmark"><span>Brindle Works</span><span class="dot"></span></div>
    <div class="person"><p class="person-name">Owen Hartley</p><p class="person-role">managing director</p></div>
    <dl class="contacts"><dt>email:</dt><dd>owen@hartleymail.com</dd><dt>skype:</dt><dd>owenbeijing</dd><dt>mobile:</dt><dd>+86 13800452718</dd></dl>
    <div class="palette"><span style="background:var(--green)"></span><span style="background:var(--purple)"></span><span style="background:var(--pink)"></span><span style="background:var(--orange)"></span></div>
  </article>
  <article class="card back set-purple" style="left:937px;top:38px">
    <div class="wordmark"><span>Brindle Works</span><span class="dot"></span></div>
    <div class="cn-name"><span>何欧文</span><small>董事总经理</small></div>
    <div class="address"><p>灯笼庭商务中心C310室 东河路</p><p>北京市朝阳区 (100020)</p><p class="en">Suite C310, Lantern Court Business Centre</p><p class="en" style="margin-top:0">Donghe Road Chaoyang District, Beijing 100020</p></div>
    <p class="web">www.brindlechina.com</p>
  </article>

  <!-- pink set -->
  <article class="card front set-pink" style="left:40px;top:571px">
    <div class="wordmark"><span>Brindle Works</span><span class="dot"></span></div>
    <div class="person"><p class="person-name">Owen Hartley</p><p class="person-role">managing director</p></div>
    <dl class="contacts"><dt>email:</dt><dd>owen@hartleymail.com</dd><dt>skype:</dt><dd>owenbeijing</dd><dt>mobile:</dt><dd>+86 13800452718</dd></dl>
    <div class="palette"><span style="background:var(--green)"></span><span style="background:var(--purple)"></span><span style="background:var(--pink)"></span><span style="background:var(--orange)"></span></div>
  </article>
  <article class="card back set-pink" style="left:299px;top:571px">
    <div class="wordmark"><span>Brindle Works</span><span class="dot"></span></div>
    <div class="cn-name"><span>何欧文</span><small>董事总经理</small></div>
    <div class="address"><p>灯笼庭商务中心C310室 东河路</p><p>北京市朝阳区 (100020)</p><p class="en">Suite C310, Lantern Court Business Centre</p><p class="en" style="margin-top:0">Donghe Road Chaoyang District, Beijing 100020</p></div>
    <p class="web">www.brindlechina.com</p>
  </article>

  <!-- orange set -->
  <article class="card front set-orange" style="left:678px;top:571px">
    <div class="wordmark"><span>Brindle Works</span><span class="dot"></span></div>
    <div class="person"><p class="person-name">Owen Hartley</p><p class="person-role">managing director</p></div>
    <dl class="contacts"><dt>email:</dt><dd>owen@hartleymail.com</dd><dt>skype:</dt><dd>owenbeijing</dd><dt>mobile:</dt><dd>+86 13800452718</dd></dl>
    <div class="palette"><span style="background:var(--green)"></span><span style="background:var(--purple)"></span><span style="background:var(--pink)"></span><span style="background:var(--orange)"></span></div>
  </article>
  <article class="card back set-orange" style="left:937px;top:571px">
    <div class="wordmark"><span>Brindle Works</span><span class="dot"></span></div>
    <div class="cn-name"><span>何欧文</span><small>董事总经理</small></div>
    <div class="address"><p>灯笼庭商务中心C310室 东河路</p><p>北京市朝阳区 (100020)</p><p class="en">Suite C310, Lantern Court Business Centre</p><p class="en" style="margin-top:0">Donghe Road Chaoyang District, Beijing 100020</p></div>
    <p class="web">www.brindlechina.com</p>
  </article>

</main>
</body>
</html>
```